Verlindo Magician

I want the business card for my business to give to people who watch that later I will be employed to show magic here is my website http://www.verlindoillusions.example/I want the interesting design , i am very opened for formal and informal, I watch a lot of design so don't stick to the common shape and form but i hope it can also be produced the thing to write on will be the same as in picture that i will upload , i also will upload the logo for you that so can be easy to useDenis CostilleMagicianMAGICIAN BALSAMO 17 rue des Tilleuls - 25000 BESANÇON contact@verlindoillusions.example tel. 0381 946 157 tel. 0674 219 503

```html
<!DOCTYPE html>
<html lang="fr">
<head>
<meta charset="utf-8">
<title>Verlindo Magician – Business Card</title>
<link href="https://fonts.googleapis.com/css2?family=Jost:wght@400;500&display=swap" rel="stylesheet">
<style>
  :root {
    --backdrop: #2a2a2a;
    --card: #ffffff;
    --ink: #1a1a1a;
    --accent: #e8412c;
    --mist: #f1f1f1;
    --rule: #3a3a3a;
  }
  * { box-sizing: border-box; margin: 0; padding: 0; }
  html, body { width: 1200px; height: 895px; overflow: hidden; }
  body {
    background: var(--backdrop);
    font-family: "Jost", "Futura", sans-serif;
    color: var(--ink);
    position: relative;
  }
  .card {
    position: absolute;
    left: 260px;
    width: 680px;
    height: 389px;
    background: var(--card);
    box-shadow: 0 10px 30px rgba(0,0,0,.45);
    overflow: hidden;
  }
  .card--front { top: 40px; }
  .card--back { top: 466px; }

  /* Front */
  .front-pattern {
    position: absolute;
    inset: 0;
    background: linear-gradient(160deg, var(--mist) 0%, #f7f7f7 45%, var(--card) 75%);
  }
  .front-brand {
    position: absolute;
    right: 60px;
    top: 130px;
    display: flex;
    flex-direction: column;
    align-items: center;
    gap: 10px;
  }
  .front-brand .portrait { width: 90px; height: 80px; }
  .wordmark {
    font-weight: 400;
    letter-spacing: 3px;
    color: var(--ink);
    font-size: 36px;
    line-height: 1;
  }

  /* Back */
  .back-brand {
    position: absolute;
    left: 70px;
    top: 70px;
    display: flex;
    flex-direction: column;
    align-items: center;
    gap: 14px;
  }
  .back-brand .portrait { width: 200px; height: 190px; }
  .portrait {
    background: linear-gradient(180deg, #3a3a3a, #0e0e0e);
    border-radius: 40% 40% 8px 8px;
  }
  .divider {
    position: absolute;
    left: 345px;
    top: 95px;
    width: 1.5px;
    height: 220px;
    background: var(--rule);
  }
  .contact {
    position: absolute;
    left: 375px;
    top: 88px;
  }
  .contact__name {
    font-weight: 500;
    font-size: 30px;
    letter-spacing: .5px;
    line-height: 1;
  }
  .contact__role {
    color: var(--accent);
    font-size: 17px;
    letter-spacing: 1px;
    margin-top: 4px;
  }
  .contact__address {
    font-size: 17px;
    line-height: 1.35;
    margin: 22px 0 0 30px;
  }
  .contact__list {
    list-style: none;
    margin: 4px 0 0 30px;
    font-size: 17px;
    line-height: 1.45;
  }
  .contact__list li { display: flex; align-items: center; gap: 10px; }
  .contact__list svg { width: 14px; height: 14px; fill: var(--accent); flex: none; }
</style>
</head>
<body>
  <section class="card card--front" aria-label="Card front">
    <div class="front-pattern" role="img" aria-label="Faint repeating pattern of the magician illustration"></div>
    <div class="front-brand">
      <div class="portrait" role="img" aria-label="Illustration of the magician holding a playing card"></div>
      <span class="wordmark">VERLINDO</span>
    </div>
  </section>

  <section class="card card--back" aria-label="Card back">
    <div class="back-brand">
      <div class="portrait" role="img" aria-label="Illustration of the magician in a dark jacket holding a playing card"></div>
      <span class="wordmark">VERLINDO</span>
    </div>
    <div class="divider"></div>
    <div class="contact">
      <h1 class="contact__name">MARC RAVOULET</h1>
      <p class="contact__role">MAGICIAN</p>
      <p class="contact__address">17 rue des Tilleuls<br>25000 BESANÇON</p>
      <ul class="contact__list">
        <li><svg viewBox="0 0 24 24"><path d="M6.6 10.8a15 15 0 0 0 6.6 6.6l2.2-2.2a1 1 0 0 1 1-.25 11.4 11.4 0 0 0 3.6.57 1 1 0 0 1 1 1V20a1 1 0 0 1-1 1A17 17 0 0 1 3 4a1 1 0 0 1 1-1h3.5a1 1 0 0 1 1 1c0 1.25.2 2.45.57 3.57a1 1 0 0 1-.25 1z"/></svg>0381 946 157</li>
        <li><svg viewBox="0 0 24 24"><path d="M6.6 10.8a15 15 0 0 0 6.6 6.6l2.2-2.2a1 1 0 0 1 1-.25 11.4 11.4 0 0 0 3.6.57 1 1 0 0 1 1 1V20a1 1 0 0 1-1 1A17 17 0 0 1 3 4a1 1 0 0 1 1-1h3.5a1 1 0 0 1 1 1c0 1.25.2 2.45.57 3.57a1 1 0 0 1-.25 1z"/></svg>0674 219 503</li>
        <li><svg viewBox="0 0 24 24"><path d="M2 5h20v14H2z M2 5l10 8 10-8" stroke="#fff" stroke-width="1.5"/></svg>contact@verlindoillusions.example</li>
        <li><svg viewBox="0 0 24 24"><circle cx="12" cy="12" r="10"/><path d="M2 12h20M12 2c3 3 3 17 0 20M12 2c-3 3-3 17 0 20" stroke="#fff" stroke-width="1.3" fill="none"/></svg>verlindoillusions.example</li>
      </ul>
    </div>
  </section>
</body>
</html>
```